High-end construction company needs a business card design

We need a modern looking business card that draws people in, is memorable and looks so good people will want to sick it on their fridges.
On the first side what is needed are:
Logo
My name - Tomasz Brelwik
Title - Managing Director
Website - www.varkelt.co.uk
Email - tomasz@varkelt.co.uk
Telephone - 020 5194 6281
Mobile - 07845139072
On the back side was is needed is a list of all the services we provide:
-Kitchen Renovations
-Bathroom Renovations
-House Renovations
-Garage Conversions
-Extensions
-Loft Conversions
-Conservatories
-Carpentry
-Tiling
-Electrical
-Plumbing & Heating
-Bricklaying
-Landscaping
-Decorating
-Plastering
We would like the colours to be the same shades as on the logo with grey or black for the words.
Target Market(s)
Anyone who needs building work done
Contact Information for Business Card
This business card is for a construction company which strives to deliver excellent service and quality.
The look and feel of the card should represent this.
Requirements
Must have
- On the first side what is needed are:
Logo
My name - Tomasz Brelwik
Title - Managing Director
Website - www.varkelt.co.uk
Email - tomasz@varkelt.co.uk
Telephone - 020 5194 6281
Mobile - 07845139072
Nice to have
- Cool looking features

```html
<!DOCTYPE html>
<html lang="en">
<head>
<meta charset="utf-8">
<title>Varkelt Construction Ltd – Business Card</title>
<link href="https://fonts.googleapis.com/css2?family=Open+Sans:wght@400;600;700&display=swap" rel="stylesheet">
<style>
  :root {
    --stage-light: #f1f1f1;
    --stage-dark: #d9d9d9;
    --green: #4a8a3c;
    --green-dark: #3f7a33;
    --green-light: #74b843;
    --paper: #f4f4f4;
    --ink: #2e2e2e;
    --white: #ffffff;
  }
  * { margin: 0; padding: 0; box-sizing: border-box; }
  html, body { width: 1200px; height: 960px; overflow: hidden; }
  body {
    position: relative;
    background: radial-gradient(ellipse at center, var(--stage-light) 0%, var(--stage-dark) 100%);
    font-family: "Open Sans", Arial, sans-serif;
  }
  .card {
    position: absolute;
    left: 330px;
    width: 550px;
    height: 357px;
    overflow: hidden;
    box-shadow: 3px 4px 6px rgba(0,0,0,0.25);
  }

  /* Services side */
  .card--services { top: 105px; background: var(--green); }
  .card__artwork {
    position: absolute;
    left: 6px; top: 45px;
    width: 340px; height: 285px;
    border-radius: 8px;
    background: linear-gradient(135deg, rgba(116,184,67,0.55) 0%, rgba(255,255,255,0.25) 60%, rgba(116,184,67,0.35) 100%);
  }
  .services {
    position: absolute;
    right: 27px; top: 32px;
    list-style: none;
    text-align: right;
    color: var(--white);
    font-size: 14px;
    line-height: 19.5px;
  }
  .services li::after {
    content: "";
    display: inline-block;
    width: 5px; height: 5px;
    margin-left: 6px;
    border-radius: 50%;
    background: var(--green-light);
    vertical-align: middle;
  }

  /* Contact side */
  .card--contact { top: 503px; background: var(--paper); }
  .brand {
    position: absolute;
    left: 47px; top: 92px;
    display: flex;
    align-items: center;
    gap: 10px;
  }
  .brand__mark { width: 16px; height: 16px; background: var(--green-light); }
  .brand__name {
    color: var(--green-light);
    font-weight: 700;
    font-size: 20px;
    line-height: 24px;
    text-transform: uppercase;
  }
  .person {
    position: absolute;
    right: 40px; top: 81px;
    text-align: right;
  }
  .person__name {
    color: var(--green);
    font-weight: 700;
    font-size: 17px;
    letter-spacing: 0.3px;
    text-transform: uppercase;
  }
  .person__title { color: var(--ink); font-size: 14px; margin-top: 2px; }
  .accent-tab {
    position: absolute;
    right: 0; top: 77px;
    width: 13px; height: 48px;
    background: var(--green);
  }
  .contact-band {
    position: absolute;
    left: 0; top: 194px;
    width: 100%; height: 121px;
    background: var(--green);
    border-bottom: 5px solid var(--green-light);
  }
  .contacts {
    position: absolute;
    left: 47px; top: 24px;
    list-style: none;
    color: var(--white);
    font-size: 14px;
    line-height: 19.5px;
  }
  .contacts li { display: flex; align-items: center; gap: 5px; }
  .contacts svg { width: 13px; height: 13px; fill: none; stroke: var(--green-light); stroke-width: 1.6; }
</style>
</head>
<body>

<section class="card card--services" aria-label="Services side">
  <div class="card__artwork" role="img" aria-label="Excavator arm reaching over house and building outlines"></div>
  <ul class="services">
    <li>Kitchen Renovations</li>
    <li>Bathroom Renovations</li>
    <li>House Renovations</li>
    <li>Garage Conversions</li>
    <li>Plumbing &amp; Heating</li>
    <li>Loft Conversions</li>
    <li>Conservatories</li>
    <li>Extensions</li>
    <li>Carpentry</li>
    <li>Electrical</li>
    <li>Bricklaying</li>
    <li>Landscaping</li>
    <li>Decorating</li>
    <li>Plastering</li>
    <li>Tiling</li>
  </ul>
</section>

<section class="card card--contact" aria-label="Contact side">
  <div class="brand">
    <span class="brand__mark"></span>
    <span class="brand__name">Varkelt<br>Construction Ltd</span>
  </div>

  <div class="person">
    <p class="person__name">Tomasz Brelwik</p>
    <p class="person__title">Managing Director</p>
  </div>
  <div class="accent-tab"></div>

  <div class="contact-band">
    <ul class="contacts">
      <li>
        <svg viewBox="0 0 16 16"><path d="M3 1.5l3 3-1.5 2a9 9 0 0 0 5 5l2-1.5 3 3-2 2C6 14 2 10 1.5 3.5z"/></svg>
        020 5194 6281
      </li>
      <li>
        <svg viewBox="0 0 16 16"><rect x="4" y="1" width="8" height="14" rx="1.5"/><line x1="7" y1="12.5" x2="9" y2="12.5"/></svg>
        07845139072
      </li>
      <li>
        <svg viewBox="0 0 16 16"><rect x="1" y="3" width="14" height="10"/><polyline points="1,3 8,9 15,3"/></svg>
        tomasz@varkelt.co.uk
      </li>
      <li>
        <svg viewBox="0 0 16 16"><circle cx="8" cy="8" r="6.5"/><ellipse cx="8" cy="8" rx="3" ry="6.5"/><line x1="1.5" y1="8" x2="14.5" y2="8"/></svg>
        www.varkelt.co.uk
      </li>
    </ul>
  </div>
</section>

</body>
</html>
```